Structural Engineering Business Card

Brookvane Drafting does residential house plans for clients in Central Florida. Would like simple but elegant business card that is appropriate for a house plan engineering company. Prefer black business card with black/white them but open to other shades of blue. I uploaded a sample card that I came across that looked good but please come up with your own creative designs.

Contact Information for Business Card

Name, Title, Phone, Email, Address, website

```html
<!DOCTYPE html>
<html lang="en">
<head>
<meta charset="utf-8">
<title>Brookvane Drafting — Business Card</title>
<link href="https://fonts.googleapis.com/css2?family=Lato:wght@400;700;900&display=swap" rel="stylesheet">
<style>
  :root {
    --backdrop: #e9e7e4;
    --card-black: #141414;
    --card-white: #ffffff;
    --ink: #111111;
    --ink-soft: #555555;
    --paper-line: #f1f1f1;
    --drawing-light: #ececec;
    --drawing-dark: #262626;
  }
  * { box-sizing: border-box; margin: 0; padding: 0; }
  html, body {
    width: 1200px; height: 992px; overflow: hidden;
    background: var(--backdrop);
    font-family: "Lato", Arial, sans-serif;
  }
  .canvas { position: relative; width: 1200px; height: 992px; }

  .card {
    position: absolute; width: 640px; height: 366px;
    border-radius: 22px; overflow: hidden;
    box-shadow: 0 14px 30px rgba(0,0,0,.18);
  }

  /* Front (black) */
  .card--front { left: 460px; top: 80px; background: var(--card-black); }
  .card--front .house-drawing {
    position: absolute; left: 300px; top: 90px; width: 320px; height: 276px;
    background: linear-gradient(160deg, var(--card-black), var(--drawing-dark));
  }
  .card--front .brand {
    position: absolute; left: 0; right: 0; top: 140px; text-align: center;
    color: #ffffff; font-weight: 900; font-size: 52px; letter-spacing: 1px;
    text-transform: uppercase; line-height: 1.05;
  }

  /* Back (white) */
  .card--back { left: 100px; top: 520px; background: var(--card-white); }
  .card--back .house-drawing {
    position: absolute; left: 150px; top: 120px; width: 290px; height: 246px;
    background: linear-gradient(180deg, var(--card-white), var(--drawing-light));
  }
  .contact-block { position: absolute; left: 40px; top: 52px; width: 300px; }
  .person-name { font-weight: 900; font-size: 30px; color: var(--ink); letter-spacing: .5px; }
  .person-title { font-size: 20px; color: var(--ink-soft); margin-top: 2px; }
  .rule { height: 1.5px; background: var(--ink); margin: 14px 0 12px; }
  .contact-list { list-style: none; }
  .contact-list li {
    display: flex; align-items: center; gap: 10px;
    font-size: 18px; color: var(--ink-soft); line-height: 1.55;
  }
  .contact-list li.phone { color: var(--ink); font-size: 21px; }
  .contact-list svg { width: 15px; height: 15px; fill: var(--ink); flex: none; }

  .card--back .brand {
    position: absolute; right: 40px; top: 72px; width: 250px; text-align: right;
    color: var(--ink); font-weight: 900; font-size: 34px;
    text-transform: uppercase; line-height: 1.05;
  }
  .office-block {
    position: absolute; right: 40px; bottom: 34px; width: 230px; text-align: right;
  }
  .office-block .rule { margin: 0 0 10px; }
  .office-name { font-size: 17px; color: var(--ink); }
  .office-address { font-size: 17px; color: var(--ink-soft); line-height: 1.4; }
</style>
</head>
<body>
<main class="canvas">

  <section class="card card--front" aria-label="Card front">
    <div class="house-drawing" role="img" aria-label="Faint architectural house elevation drawing on a grid"></div>
    <div class="brand">Brookvane<br>Drafting</div>
  </section>

  <section class="card card--back" aria-label="Card back">
    <div class="house-drawing" role="img" aria-label="Faint architectural house elevation drawing on a grid"></div>

    <div class="contact-block">
      <h1 class="person-name">DANIEL HARLOW</h1>
      <p class="person-title">Founder &amp; CEO</p>
      <div class="rule"></div>
      <ul class="contact-list">
        <li class="phone">
          <svg viewBox="0 0 24 24" aria-hidden="true"><path d="M6.6 10.8a15 15 0 0 0 6.6 6.6l2.2-2.2a1 1 0 0 1 1-.25 11.4 11.4 0 0 0 3.6.57 1 1 0 0 1 1 1V20a1 1 0 0 1-1 1A17 17 0 0 1 3 4a1 1 0 0 1 1-1h3.5a1 1 0 0 1 1 1c0 1.25.2 2.45.57 3.57a1 1 0 0 1-.25 1z"/></svg>
          (123) 456-7890
        </li>
        <li>
          <svg viewBox="0 0 24 24" aria-hidden="true"><path d="M2 5h20v14H2zm2 2v.5l8 5 8-5V7l-8 5z"/></svg>
          office@brookvane.com
        </li>
        <li>
          <svg viewBox="0 0 24 24" aria-hidden="true"><circle cx="12" cy="12" r="10"/></svg>
          www.brookvane.com
        </li>
      </ul>
    </div>

    <div class="brand">Brookvane<br>Drafting</div>

    <div class="office-block">
      <div class="rule"></div>
      <p class="office-name">Brookvane Drafting Group</p>
      <p class="office-address">Your Address, City<br>State, Zip 1235</p>
    </div>
  </section>

</main>
</body>
</html>
```